New Business Card Design Project

We require a business card design for Vexalund, a newly established Indian company.
Our focus is on the development, manufacturing, and export of a diverse array of pharmaceutical products on a global scale. The card should convey a professional appearance, as our primary markets are in Africa, China, and Southeast Asian nations.
We envision a two-sided business card, with the reverse side dedicated to a logo set against a solid color or an elegantly designed pattern. The corners should be rounded. We would appreciate seeing both horizontal and vertical design options. We trust the designer to utilize their expertise in creating this design.

The content for the business card is included in the attached Word file.

Target Market(s)

Our primary markets are in Africa, China, and Southeast Asian, Latin America, Maldives, Sri Lanka

Industry/Entity Type

Pharmaceutical Manufacturing and Export

Contact Information for Business Card

Colors

Designer to choose colors to be used in the design.

Requirements
Must have
• The reverse side of the business card features solely the logo along with the tagline, "Healing for All."
Should not have
• The logo should not exceed two instances, encompassing both the front and back sides of the card.

```html
<!DOCTYPE html>
<html lang="en">
<head>
<meta charset="utf-8">
<title>Vexalund Business Card</title>
<link rel="stylesheet" href="https://fonts.googleapis.com/css2?family=Red+Hat+Display:wght@600;700&family=Karla:wght@400&display=swap">
<style>
  :root {
    --stage: #2a2a2a;
    --brand-blue: #259fd6;
    --brand-blue-deep: #1f90c6;
    --accent-red: #e2533f;
    --paper: #eeeeee;
    --paper-shade: #d9d9d9;
    --ink: #2b2b2b;
    --white: #f4f4f4;
  }
  * { box-sizing: border-box; margin: 0; padding: 0; }
  html, body { width: 1200px; height: 1138px; overflow: hidden; }
  body {
    background: var(--stage);
    position: relative;
    font-family: "Karla", sans-serif;
  }
  .card {
    position: absolute;
    border-radius: 18px;
    overflow: hidden;
  }
  .card--front {
    left: 274px; top: 186px; width: 623px; height: 376px;
    background: linear-gradient(160deg, var(--brand-blue) 0%, var(--brand-blue-deep) 100%);
  }
  .brand-lockup {
    position: absolute;
    left: 0; right: 0; top: 226px;
    text-align: center;
    color: var(--white);
  }
  .brand-name {
    font-family: "Red Hat Display", sans-serif;
    font-weight: 700;
    font-size: 66px;
    line-height: 1;
  }
  .card-tagline {
    margin-top: 10px;
    font-family: "Karla", sans-serif;
    font-size: 15px;
    letter-spacing: 3px;
    color: var(--white);
  }
  .card--back {
    left: 276px; top: 608px; width: 618px; height: 374px;
    background: linear-gradient(170deg, var(--paper) 0%, var(--paper) 60%, var(--paper-shade) 100%);
  }
  .back-panel { position: absolute; inset: 0; }
  .back-brand {
    position: absolute;
    left: 0; width: 330px; top: 218px;
    text-align: center;
    font-family: "Red Hat Display", sans-serif;
    font-weight: 700;
    font-size: 54px;
    color: var(--white);
    line-height: 1;
  }
  .contact {
    position: absolute;
    left: 372px; top: 88px;
    color: var(--ink);
  }
  .contact-name {
    font-family: "Red Hat Display", sans-serif;
    font-weight: 700;
    font-size: 25px;
    color: var(--brand-blue);
    line-height: 1;
  }
  .contact-role { font-size: 15px; margin-top: 6px; }
  .contact-list { list-style: none; margin-top: 31px; }
  .contact-list li {
    display: flex; align-items: center; gap: 12px;
    font-size: 15.5px; height: 23px;
  }
  .contact-list svg { width: 16px; height: 14px; flex: none; }
  .contact-address { font-size: 15px; line-height: 22.5px; margin-top: 8px; }
</style>
</head>
<body>
  <section class="card card--front">
    <div class="brand-lockup">
      <div class="brand-name">Vexalund</div>
      <div class="card-tagline">Healing for All</div>
    </div>
  </section>

  <section class="card card--back">
    <svg class="back-panel" viewBox="0 0 618 374" preserveAspectRatio="none" aria-hidden="true">
      <path d="M0 0 H266 Q420 187 284 374 H0 Z" fill="#e2533f"/>
      <path d="M0 0 H260 Q406 187 252 374 H0 Z" fill="#259fd6"/>
    </svg>
    <div class="back-brand">Vexalund</div>

    <div class="contact">
      <div class="contact-name">Arvind K. Solanke</div>
      <div class="contact-role">CEO, Vexalund</div>
      <ul class="contact-list">
        <li>
          <svg viewBox="0 0 16 14" aria-hidden="true"><path d="M1 4 Q8 -1 15 4 L13 6 L11 4.5 H5 L3 6 Z M4 7 H12 L14 13 H2 Z" fill="#e2533f"/></svg>
          +91-9876501234
        </li>
        <li>
          <svg viewBox="0 0 16 14" aria-hidden="true"><rect x="1" y="2" width="14" height="10" fill="#e2533f"/><path d="M1.5 2.5 L8 8 L14.5 2.5 M1.5 11.5 L6 7 M14.5 11.5 L10 7" stroke="#eeeeee" stroke-width="1.2" fill="none"/></svg>
          asolanke@vexalund.com
        </li>
        <li>
          <svg viewBox="0 0 16 14" aria-hidden="true"><circle cx="8" cy="7" r="6" fill="#e2533f"/><path d="M2 7 H14 M8 1 V13 M3.5 4 H12.5 M3.5 10 H12.5" stroke="#eeeeee" stroke-width="0.9" fill="none"/><ellipse cx="8" cy="7" rx="2.6" ry="6" stroke="#eeeeee" stroke-width="0.9" fill="none"/></svg>
          https://vexalund.com
        </li>
      </ul>
      <p class="contact-address">12, Neelkamal Colony,<br>Sundarpur-440118 (INDIA)</p>
    </div>
  </section>
</body>
</html>
```